Webdesign für Sexualpädagogik
Zielgruppe
- Sexualpädagogik, Beratung und Sexualtherapie
- Vorträge und Seminare für Unternehmen / Institutionen Vorträge Sexualität in der Pflege / im Alter / Grenzen wahrnehmen
- Wechseljahreberatung, Beratung in der Lebensmitte
- ZIelgruppe: Menschen, die sich weiternetwickeln möchten, die Problme mit ihrer Sexualität haben, Paare, Jugendliche
letztes Interview in der Zeitung: https://www.talpost-beispiel.ch/nachrichtenblatt/zeitung/frontal-interview/sexualitaet-hoert-nicht-beim-eintritt-ins-spital-auf/
Aufgabenstellung
- bestehende Internetseite siehe unten: Schrift ist Especial Key von Tauwerk Mitte
- auf dem Briefpapier bisher noch der Fachbuchhandel und Onlinhandel, aber beides nicht mehr
- Bilder zum Thema bereist vorhanden
- für Werbeflyer habe ich die Therapie in dunkelblau gehalten udn in der sexualpädagogik in hellblau
der kramkiste wird aus der website entfernet

```html
<!DOCTYPE html>
<html lang="de">
<head>
<meta charset="utf-8">
<title>Tauwerk Mitte – Sexualtherapie</title>
<link href="https://fonts.googleapis.com/css2?family=Libre+Baskerville&family=Crimson+Text:wght@400;600&family=Raleway:wght@300;400;500&display=swap" rel="stylesheet">
<style>
:root{
  --ink:#2b2b2b;
  --text:#555;
  --muted:#8a8a8a;
  --line:#cfcfcf;
  --grey-band:#ececec;
  --white:#fff;
  --hero-a:#c9a49a;
  --hero-b:#3d7a88;
  --orange:#f08a24;
}
*{box-sizing:border-box;margin:0;padding:0}
html,body{width:1200px;height:4008px;overflow:hidden;background:var(--white)}
body{position:relative;font-family:"Raleway",sans-serif;color:var(--text)}
.abs{position:absolute}
.serif{font-family:"Libre Baskerville",serif}
.book{font-family:"Crimson Text",serif}
.center{text-align:center}
.photo{position:absolute}

/* header */
.brand-name{left:26px;top:26px;font-size:16px;font-weight:500;color:var(--ink);line-height:1.1;letter-spacing:.3px}
.brand-name small{display:block;font-size:13px;font-weight:400;letter-spacing:.5px}
.social{position:absolute;display:flex;gap:14px}
.social span{display:block;border-radius:50%;background:var(--ink)}
.logo-word{left:0;width:1200px;top:140px;font-size:52px;color:var(--ink);text-align:center;font-family:"Libre Baskerville",serif}
.nav{left:0;top:300px;width:1200px;height:56px;border-top:2px solid #e3e3e3}
.nav span{position:absolute;top:22px;transform:translateX(-50%);font-size:11px;color:var(--ink);letter-spacing:.3px}

/* hero */
.hero{left:0;top:355px;width:1200px;height:563px;background:linear-gradient(90deg,var(--hero-a) 0%,#d7c1b6 35%,#7ba6b1 60%,var(--hero-b) 100%)}
.hero-frame{left:576px;top:432px;width:529px;height:408px;border:1px solid rgba(255,255,255,.7)}
.hero-quote{left:576px;width:529px;top:480px;font-size:48px;line-height:58px;color:var(--white);text-align:center}
.hero-more{left:576px;width:529px;top:830px;text-align:center;color:var(--white);font-size:15px;background:transparent}
.hero-more span{background:#78a2ad;padding:0 10px}
.arrow{position:absolute;top:620px}

/* welcome */
.welcome{left:0;top:918px;width:1200px;height:334px;background:var(--grey-band)}
.welcome h1{position:absolute;top:60px;width:1200px;text-align:center;font-family:"Libre Baskerville",serif;font-weight:400;font-size:38px;color:var(--ink)}
.welcome p{position:absolute;left:109px;width:988px;text-align:center;font-size:15.5px;line-height:22px;font-weight:300;color:#666}

/* service cards */
.card-label{position:absolute;height:50px;background:var(--white);border:1px solid #ddd;font-size:14px;color:var(--ink);text-align:center;line-height:48px}

/* about */
.about-title{left:106px;width:650px;top:1705px;text-align:center;font-family:"Libre Baskerville",serif;font-size:38px;color:var(--ink)}
.about-text{left:106px;width:650px;font-size:16px;line-height:22px;font-weight:300;color:#555}
.btn{position:absolute;border:1px solid var(--line);background:var(--white);color:var(--ink);text-align:center;font-size:13px}
.host-frame{left:817px;top:1730px;width:271px;height:402px;border:1px solid #bbb}
.host-title{left:801px;width:302px;top:1940px;text-align:center;font-family:"Libre Baskerville",serif;font-size:20px;color:var(--ink)}
.host-text{left:835px;width:236px;top:1982px;text-align:center;font-family:"Crimson Text",serif;font-size:12.5px;line-height:16.5px;color:var(--muted)}
.host-cta{left:801px;width:302px;top:2125px;text-align:center;font-size:11px;color:var(--ink);letter-spacing:.3px}
.host-cta span{background:var(--white);padding:0 14px}

/* posts */
.cat{position:absolute;width:302px;text-align:center;font-size:11px;color:var(--muted);letter-spacing:.5px}
.post-title{position:absolute;width:302px;text-align:center;font-family:"Crimson Text",serif;font-size:20px;line-height:23px;color:var(--ink)}
.date{position:absolute;width:302px;text-align:center;font-size:10px;color:var(--muted)}
.excerpt{position:absolute;width:302px;font-family:"Crimson Text",serif;font-size:13.5px;line-height:16px;color:var(--muted);text-align:justify}
.excerpt b{font-weight:600;color:#666}

/* sidebar */
.rule{position:absolute;height:1px;background:#ddd}
.side-head{position:absolute;left:801px;width:302px;text-align:center;font-size:14px;color:#777;letter-spacing:.5px}
.side-line{position:absolute;left:801px;width:302px;text-align:center;font-family:"Crimson Text",serif;font-size:18px;color:var(--ink)}
.side-small{position:absolute;left:801px;width:302px;text-align:center;font-size:10px;color:var(--muted)}
.nl-text{left:843px;width:218px;top:3298px;text-align:center;font-family:"Crimson Text",serif;font-size:15px;line-height:23px;color:var(--ink);font-weight:600}
.field{position:absolute;border:1px solid #aaa;background:var(--white);font-size:8px;color:#555;padding-left:8px;line-height:20px}

/* footer */
.footer{left:0;top:3600px;width:1200px;height:357px;background:var(--grey-band)}
.map{left:65px;top:3630px;width:279px;height:299px;background:linear-gradient(135deg,#e4e6e8,#f3f3f1 55%,#dfe9d3)}
.foot-head{left:378px;top:3633px;font-size:14px;line-height:17px;color:var(--ink)}
.foot-row{position:absolute;left:378px;font-size:11px;color:var(--ink);display:flex;align-items:center;gap:8px}
.foot-plan{left:378px;width:386px;top:3792px;font-size:8.5px;line-height:12px;color:#666}
.contact-head{left:801px;top:3633px;font-size:14px;color:var(--ink)}
.footer .field{background:transparent}
.bottom-bar span{position:absolute;top:3984px;font-size:11px;color:var(--ink);transform:translateX(-50%)}
</style>
</head>
<body>

<header>
  <div class="abs brand-name">LENA MARBACH<small>SEXUALTHERAPEUTIN</small></div>
  <div class="social" style="left:976px;top:30px;gap:20px" aria-label="Soziale Netzwerke">
    <span style="width:26px;height:26px"></span><span style="width:26px;height:26px"></span><span style="width:26px;height:26px"></span><span style="width:26px;height:26px"></span>
  </div>
  <div class="abs logo-word">Tauwerk Mitte</div>
  <nav class="abs nav">
    <span style="left:124px">HOME</span>
    <span style="left:215px">ÜBER MICH</span>
    <span style="left:345px">SEXUALBERATUNG</span>
    <span style="left:503px">SEXUALPÄDAGOGIK</span>
    <span style="left:683px">WECHSELJAHRBERATUNG</span>
    <span style="left:826px">SEMINAR</span>
    <span style="left:916px">NEWS</span>
    <span style="left:997px">BLOG</span>
    <span style="left:1077px">KONTAKT</span>
  </nav>
</header>

<section>
  <div class="abs hero" role="img" aria-label="Foto: Hände halten einen herzförmigen grauen Stein"></div>
  <div class="abs hero-frame"></div>
  <div class="abs hero-quote serif">Wenn wir uns selbst nicht lieben, können wir auch keinen anderen Menschen lieben.</div>
  <div class="abs hero-more"><span>MEHR ERFAHREN</span></div>
  <svg class="arrow" style="left:55px" width="20" height="34" viewBox="0 0 20 34"><path d="M17 2 L3 17 L17 32" fill="none" stroke="#fff" stroke-width="3"/></svg>
  <svg class="arrow" style="left:1146px" width="20" height="34" viewBox="0 0 20 34"><path d="M3 2 L17 17 L3 32" fill="none" stroke="#fff" stroke-width="3"/></svg>
</section>

<section class="abs welcome">
  <h1>Wilkommen!</h1>
  <p style="top:137px">Lorem ipsum dolor sit amet, consectetur adipiscing elit, sed do eiusmod tempor incididunt ut labore et dolore magna aliqua. Praesent elementum facilisis leo vel fringilla est ullamcorper. Id ornare arcu odio ut sem. Quam lacus suspendisse faucibus interdum posuere lorem.</p>
  <p style="top:222px">Duis ultricies lacus sed turpis. Ultricies mi quis hendrerit dolor magna eget est lorem. Tellus orci ac auctor augue mauris augue neque. Lorem ipsum dolor sit amet consectetur adipiscing elit pellentesque habitant.</p>
</section>

<section>
  <div class="photo" style="left:106px;top:1330px;width:302px;height:282px;background:linear-gradient(135deg,#a88a6c,#6a5446)" role="img" aria-label="Foto: lachendes junges Paar"></div>
  <div class="card-label" style="left:153px;top:1587px;width:208px">SEXUALBERATUNG</div>
  <div class="photo" style="left:454px;top:1330px;width:302px;height:282px;background:linear-gradient(135deg,#e3d6c8,#c9ab95)" role="img" aria-label="Foto: lachende Frau mit blondem Haar"></div>
  <div class="card-label" style="left:500px;top:1587px;width:208px">WECHSELJAHRBERATUNG</div>
  <div class="photo" style="left:801px;top:1330px;width:302px;height:282px;background:linear-gradient(135deg,#9fb6c2,#5d7280)" role="img" aria-label="Foto: junges Paar im Freien"></div>
  <div class="card-label" style="left:849px;top:1587px;width:208px">SEXUALPÄDAGOGIK</div>
</section>

<section>
  <div class="abs about-title">Über Liebe lernen</div>
  <p class="abs about-text" style="top:1774px">Das Ziel ist die Zufriedenheit von Ihnen und Ihrem Partner. Verwirklichen Sie Ideen, Träume und Phantasien. Nutzen Sie es als Anregung für eine erfüllte und lebendige Partnerschaft und Sexualität, für ein zufriedenes und glückliches Selbst und Miteinander.</p>
  <p class="abs about-text" style="top:1894px">Denn nur, wenn man sich selbst liebt, kann man auch die Partnerin / den Partner lieben. Verzaubern und verführen Sie mit Spass und Freude um des Verführens Willen. Die Idee basiert auf der Ganzheit der Menschen und Partnerschaft und der Individualität jeder und jedes Einzelnen und deren Partnerschaft. Im ganz besonderen möchte ich Frauen ansprechen, denen ich Mut machen möchte, sich selbst, ihren Körper, Geist und ihre sexuellen Wünsche kennenzulernen und zu entdecken.</p>
  <div class="btn" style="left:341px;top:2062px;width:207px;height:50px;line-height:48px;font-size:14px">MEHR ERFAHREN</div>

  <div class="photo" style="left:801px;top:1713px;width:302px;height:201px;background:linear-gradient(135deg,#d9d2c6,#a79b8e)" role="img" aria-label="Foto: Porträt der Therapeutin mit Brille"></div>
  <div class="abs host-frame"></div>
  <div class="abs host-title">Hallo, ich bin Lena</div>
  <p class="abs host-text">Lorem ipsum dolor sit amet, consectetur adipiscing elit, sed do eiusmod tempor incididunt ut labore et dolore magna aliqua. Praesent elementum facilisis leo vel fringilla est ullamcorper. Id ornare arcu odio ut sem. Quam lacus suspendisse faucibus interdum posuere lorem.</p>
  <div class="abs host-cta"><span>TERMIN VEREINBARUNG</span></div>
</section>

<section>
  <!-- row one -->
  <div class="photo" style="left:106px;top:2214px;width:302px;height:283px;background:linear-gradient(160deg,#f5a04a,var(--orange))" role="img" aria-label="Foto: Therapeutin sitzt auf einer orangen Treppe"></div>
  <div class="cat" style="left:106px;top:2521px">NEWS</div>
  <div class="post-title" style="left:106px;top:2550px">Sexualität hört nicht beim<br>Eintritt ins Spital auf</div>
  <div class="date" style="left:106px;top:2625px">26. JULI, 2018</div>
  <p class="excerpt" style="left:106px;top:2655px">Vorfälle wie der sexuelle Übergriff eines Pflegers auf eine demente Frau im Altersheim von Brig-Glis schockieren. Allerdings sind solche Übergriffe die Ausnahme. Denn «in den meisten Fällen von sexueller Belästigung und Übergriffen im Pflegebereich sind die Pflegenden die Opfer»…</p>
  <div class="btn" style="left:187px;top:2809px;width:143px;height:34px;line-height:32px;font-size:11px">WEITERLESEN</div>

  <div class="photo" style="left:454px;top:2214px;width:302px;height:283px;background:linear-gradient(135deg,#9fb6c2,#5d7280)" role="img" aria-label="Foto: junges Paar im Freien"></div>
  <div class="cat" style="left:454px;top:2521px">SEMINAR</div>
  <div class="post-title" style="left:454px;top:2550px">Nächste Seminare:<br>Wechseljahre - Heiss Geschüttelt, nicht kalt gerührt</div>
  <div class="date" style="left:454px;top:2625px">02. MAI, 2018</div>
  <p class="excerpt" style="left:470px;width:270px;top:2655px">Ein spannendes Tagesseminar über die Wechselbäder der Gefühle, über Hormone, Orientierung, Hilfen und Möglichkeiten.<br><br><b>Datum:</b> 02.06.2018 Seminar von 9.00 – 16.00<br><b>Ort:</b> Bildungshaus Seeblick, 3900 Visp<br><b>Kosten:</b> CHF 149.00, inkl.…</p>
  <div class="btn" style="left:534px;top:2809px;width:140px;height:34px;line-height:32px;font-size:11px">MEHR ERFAHREN</div>

  <!-- row two -->
  <div class="photo" style="left:106px;top:2904px;width:302px;height:283px;background:linear-gradient(160deg,#f5a04a,var(--orange))" role="img" aria-label="Foto: Therapeutin sitzt auf einer orangen Treppe"></div>
  <div class="cat" style="left:106px;top:3211px">NEWS</div>
  <div class="post-title" style="left:106px;top:3240px">Sexualität hört nicht beim<br>Eintritt ins Spital auf</div>
  <div class="date" style="left:106px;top:3315px">26. JULI, 2018</div>
  <p class="excerpt" style="left:106px;top:3345px">Vorfälle wie der sexuelle Übergriff eines Pflegers auf eine demente Frau im Altersheim von Brig-Glis schockieren. Allerdings sind solche Übergriffe die Ausnahme. Denn «in den meisten Fällen von sexueller Belästigung und Übergriffen im Pflegebereich sind die Pflegenden die Opfer»…</p>
  <div class="btn" style="left:187px;top:3498px;width:143px;height:34px;line-height:32px;font-size:11px">WEITERLESEN</div>

  <div class="photo" style="left:454px;top:2904px;width:302px;height:283px;background:linear-gradient(135deg,#9fb6c2,#5d7280)" role="img" aria-label="Foto: junges Paar im Freien"></div>
  <div class="cat" style="left:454px;top:3211px">SEMINAR</div>
  <div class="post-title" style="left:454px;top:3240px">Nächste Seminare:<br>Wechseljahre - Heiss Geschüttelt, nicht kalt gerührt</div>
  <div class="date" style="left:454px;top:3315px">02.MAI, 2018</div>
  <p class="excerpt" style="left:470px;width:270px;top:3345px">Ein spannendes Tagesseminar über die Wechselbäder der Gefühle, über Hormone, Orientierung, Hilfen und Möglichkeiten.<br><br><b>Datum:</b> 02.06.2018 Seminar von 9.00 – 16.00<br><b>Ort:</b> Bildungshaus Seeblick, 3900 Visp<br><b>Kosten:</b> CHF 149.00, inkl.…</p>
  <div class="btn" style="left:534px;top:3498px;width:140px;height:34px;line-height:32px;font-size:11px">MEHR ERFAHREN</div>
</section>

<aside>
  <div class="rule" style="left:801px;top:2197px;width:302px"></div>
  <div class="social" style="left:890px;top:2233px;gap:16px" aria-label="Soziale Netzwerke">
    <span style="width:16px;height:16px;background:#444"></span><span style="width:16px;height:16px;background:#444"></span><span style="width:16px;height:16px;background:#444"></span><span style="width:16px;height:16px;background:#444"></span>
  </div>
  <div class="side-head" style="top:2320px">NÄCHSTE SEMINARE</div>
  <div class="side-line" style="top:2370px">02.06.2018 • Visp</div>
  <div class="side-line" style="top:2398px">Thema: Wechseljahre</div>
  <div class="side-line" style="top:2452px">22.11.2018 • St. Gallen</div>
  <div class="side-line" style="top:2480px">Thema: Sexualität</div>
  <div class="rule" style="left:843px;top:2533px;width:218px"></div>
  <div class="side-head" style="top:2572px">LETZTE IN BLOG</div>
  <div class="photo" style="left:857px;top:2617px;width:200px;height:187px;background:linear-gradient(135deg,#e3d6c8,#c9ab95)" role="img" aria-label="Foto: lachende Frau mit blondem Haar"></div>
  <div class="side-line" style="top:2824px">Ist Liebe lernbar?</div>
  <div class="side-small" style="top:2855px">02. MAI, 2018</div>
  <div class="photo" style="left:857px;top:2914px;width:200px;height:186px;background:linear-gradient(135deg,#a88a6c,#6a5446)" role="img" aria-label="Foto: lachendes junges Paar"></div>
  <div class="side-line" style="top:3126px;line-height:20px">Das Ziel und<br>die Philosophie</div>
  <div class="side-small" style="top:3178px">19. JUNI, 2018</div>
  <div class="rule" style="left:843px;top:3208px;width:218px"></div>
  <div class="side-head" style="top:3255px">NEWSLETTER</div>
  <p class="abs nl-text">Sie möchten über Neuigkeiten informiert sein und sind an Kursen und / oder Weiterbildungen interessiert?</p>
  <div class="field" style="left:843px;top:3404px;width:230px;height:22px">NAME</div>
  <div class="field" style="left:843px;top:3443px;width:230px;height:22px">E-MAIL ADRESSE</div>
  <div class="field" style="left:843px;top:3481px;width:97px;height:18px;line-height:16px">EINTRAGEN</div>
  <div class="rule" style="left:843px;top:3538px;width:218px"></div>
</aside>

<footer>
  <div class="abs footer"></div>
  <div class="abs map" role="img" aria-label="Karte: Lage der Fachstelle"></div>
  <div class="abs foot-head">FACHSTELLE FÜR SEXUALPÄDAGOGIK<br>UND BERATUNG</div>
  <div class="foot-row" style="top:3683px">
    <svg width="10" height="14" viewBox="0 0 10 14"><path d="M5 0C2.2 0 0 2.2 0 5c0 3.8 5 9 5 9s5-5.2 5-9c0-2.8-2.2-5-5-5zm0 7a2 2 0 1 1 0-4 2 2 0 0 1 0 4z" fill="#222"/></svg>LINDENWEG 12, 3900 BRIG</div>
  <div class="foot-row" style="top:3707px">
    <svg width="12" height="12" viewBox="0 0 12 12"><path d="M2.4 0.5 4.3 3 3.2 4.4c.8 1.7 2.2 3.1 3.9 3.9L8.5 7.2 11 9.1 10 11.3C4.9 11 .9 7 .5 1.6z" fill="#222"/></svg>+41 (0)79 123 45 67</div>
  <div class="foot-row" style="top:3731px">
    <svg width="13" height="10" viewBox="0 0 13 10"><rect width="13" height="10" fill="#222"/><path d="M0.5 0.8 6.5 5.5 12.5 0.8" fill="none" stroke="#fff" stroke-width="1.2"/></svg>info@tauwerk-mitte.ch</div>
  <div class="abs" style="left:378px;top:3774px;font-size:11px;color:var(--ink)">LAGEPLAN</div>
  <p class="abs foot-plan">Wenn Sie vom Bahnhof kommen, gehen Sie links am Platz vorbei und folgen der Hauptstrasse bis zur zweiten Kreuzung. Dort biegen Sie rechts ab und fahren weiter bis zum kleinen Parkplatz hinter der Post. Nach etwa sechzig Metern sehen Sie links ein Schild mit unserem Namen. Folgen Sie dem Weg bis zum Eingang, wo Sie im Erdgeschoss klingeln. Bei Fragen rufen Sie uns gerne vorher an.</p>

  <div class="abs contact-head">KONTAKT MIT UNS</div>
  <div class="field" style="left:801px;top:3664px;width:302px;height:22px">NAME</div>
  <div class="field" style="left:801px;top:3703px;width:302px;height:22px">E-MAIL ADRESSE</div>
  <div class="field" style="left:801px;top:3741px;width:302px;height:22px">TELEFON</div>
  <div class="field" style="left:801px;top:3781px;width:302px;height:112px">NACHRICHT</div>
  <div class="field" style="left:1010px;top:3909px;width:93px;height:25px;text-align:center;padding:0;font-size:11px;line-height:23px">SENDEN</div>

  <div class="bottom-bar">
    <span style="left:482px">MENU</span>
    <span style="left:576px">IMPRESSUM</span>
    <span style="left:692px">DATENSCHUTZ</span>
  </div>
</footer>

</body>
</html>
```